BRIGHT RIVER POWER.

I'd like my business logo.
contact name: Dennis Halvorsen
phone:0438759164
email: info@brightriverpower.net.au
website: www.brightriverpower.net.au

services:
solar
battery storage
LED lighting
energy saving solutions
general electrical
I'd like the design to look professional

Target Market(s)

Everyone

Industry/Entity Type

Business

Contact Information for Business Card

as described above

Requirements
Must have
• Id like the colours and the design to work well with my logo.

```html
<!DOCTYPE html>
<html lang="en">
<head>
<meta charset="utf-8">
<title>Bright River Power – Business Card</title>
<link href="https://fonts.googleapis.com/css2?family=Lato:ital,wght@0,400;0,700;0,900;1,400;1,700&display=swap" rel="stylesheet">
<style>
  :root {
    --page-bg: #e6e7e8;
    --card-top: #f7f7f7;
    --brand-green: #4f9a2b;
    --band-green: #79b833;
    --orange: #e87a1c;
    --ink: #333333;
    --ink-soft: #3d2a1a;
    --muted: #f3d2b4;
    --white: #ffffff;
  }
  * { margin: 0; padding: 0; box-sizing: border-box; }
  html, body { width: 1200px; height: 970px; overflow: hidden; }
  body {
    background: var(--page-bg);
    font-family: "Lato", Arial, sans-serif;
    position: relative;
  }
  .card {
    position: absolute;
    left: 100px; top: 187px;
    width: 1000px; height: 596px;
    background: var(--card-top);
    overflow: hidden;
    box-shadow: 0 6px 22px rgba(0,0,0,0.18);
  }
  .card-shapes { position: absolute; inset: 0; }
  .brand {
    position: absolute;
    top: 92px; left: 0; width: 100%;
    display: flex; justify-content: center; align-items: center; gap: 16px;
  }
  .brand-dot {
    width: 40px; height: 40px; border-radius: 50%;
    background: var(--orange);
  }
  .brand-name {
    font-weight: 900; font-size: 46px; letter-spacing: 1px;
    color: var(--brand-green);
  }

  /* Services column: right edge sits left of the divider */
  .services-title {
    position: absolute; right: 563px; top: 295px;
    font-style: italic; font-weight: 700; font-size: 20px; line-height: 28px;
    color: var(--muted); text-decoration: underline; text-underline-offset: 4px;
    white-space: nowrap;
  }
  .services {
    position: absolute; right: 559px; top: 363px;
    list-style: none; text-align: right;
  }
  .services li {
    font-weight: 700; font-size: 20px; color: var(--ink);
    height: 37px; line-height: 28px; white-space: nowrap;
  }
  .services li::after {
    content: ""; display: inline-block;
    width: 8px; height: 8px; border-radius: 50%;
    background: var(--muted); margin-left: 14px; vertical-align: middle;
  }
  .divider {
    position: absolute; left: 478px; top: 266px;
    width: 3px; height: 290px; background: var(--muted);
  }

  /* Contact column */
  .contact-name {
    position: absolute; left: 517px; top: 292px;
    font-weight: 700; font-size: 29px; line-height: 36px;
    color: var(--white); white-space: nowrap;
  }
  .contact-role {
    position: absolute; left: 518px; top: 331px;
    font-style: italic; font-size: 20px; line-height: 26px;
    color: var(--ink-soft); white-space: nowrap;
  }
  .contact-line {
    position: absolute; left: 517px;
    display: flex; align-items: center; gap: 10px;
    font-size: 21px; line-height: 30px; height: 30px;
    color: var(--ink-soft); white-space: nowrap;
  }
  .contact-line.phone { top: 422px; }
  .contact-line.email { top: 468px; }
  .contact-line svg { width: 26px; height: 22px; flex: none; }
  .contact-web {
    position: absolute; left: 519px; top: 508px;
    font-weight: 700; font-size: 23px; line-height: 30px;
    color: var(--muted); white-space: nowrap;
  }
</style>
</head>
<body>
  <div class="card">
    <svg class="card-shapes" width="1000" height="596" viewBox="0 0 1000 596">
      <defs>
        <linearGradient id="orangeFill" x1="0" y1="0" x2="1" y2="1">
          <stop offset="0" stop-color="#f0953a"/>
          <stop offset="1" stop-color="#e06f12"/>
        </linearGradient>
      </defs>
      <path class="band-green" d="M0 272 C 300 150, 680 150, 1000 300 L1000 596 L0 596 Z" fill="var(--band-green)"/>
      <path class="panel-orange" d="M0 288 C 300 168, 680 168, 1000 318 L1000 596 L0 596 Z" fill="url(#orangeFill)"/>
    </svg>

    <div class="brand">
      <span class="brand-dot"></span>
      <span class="brand-name">BRIGHT RIVER POWER</span>
    </div>

    <div class="services-title">Our Services:</div>
    <ul class="services">
      <li>Solar</li>
      <li>LED Lighting</li>
      <li>Battery Storage</li>
      <li>General Electrical</li>
      <li>Energy Saving Solutions</li>
    </ul>

    <div class="divider"></div>

    <div class="contact-name">Dennis Halvorsen</div>
    <div class="contact-role">Owner / Founder</div>
    <div class="contact-line phone">
      <svg viewBox="0 0 26 22" aria-hidden="true"><path d="M2 8 C2 3 24 3 24 8 L20 10 L18 7 L8 7 L6 10 Z" fill="var(--ink-soft)"/><path d="M7 10 L19 10 L22 19 L4 19 Z" fill="var(--ink-soft)"/><circle cx="13" cy="14" r="2.6" fill="var(--orange)"/></svg>
      <span>0438759164</span>
    </div>
    <div class="contact-line email">
      <svg viewBox="0 0 26 22" aria-hidden="true"><rect x="2" y="4" width="22" height="15" fill="var(--white)"/><path d="M2 4 L13 13 L24 4" fill="none" stroke="var(--orange)" stroke-width="2"/></svg>
      <span>info@brightriverpower.net.au</span>
    </div>
    <div class="contact-web">www.brightriverpower.net.au</div>
  </div>
</body>
</html>
```